Indy Film Production Company/Studio

We need a business card designed from an existing logo. We are a digital studio/production company that caters to creating genre entertainment, like Action, Horror, and martial arts. The card along with the logo will be used to Brand the company from letter heads to banners. The design will also be used for postcards and Brochures. It should be professional and masculine.
Updates

Thank you to all the designers who have participated. I'm narrowing down who it will be. Thank you again.

Target Market(s)

Investors, Networks, Producers, and actors

Industry/Entity Type

Film Production

Contact Information for Business Card

Teodoro Valbuena
Producer/Writer/Director
www.kestrelpicturehouse.example

Requirements
Must have
• Website address, Facebook icon and Twitter icon possibly in the back of the card.
Nice to have
• Logline of Company: Follow The Action.

```html
<!DOCTYPE html>
<html lang="en">
<head>
<meta charset="utf-8">
<title>Kestrel Picture House – Business Card</title>
<link rel="stylesheet" href="https://fonts.googleapis.com/css2?family=Source+Sans+3:wght@400;600;700&display=swap">
<style>
  :root {
    --page-bg: #d8d4d1;
    --card-red: #d0141f;
    --card-red-deep: #b50d18;
    --frost: #c9c7c5;
    --frost-edge: #b3b1af;
    --stripe: #f4eeec;
    --foil: #efe6e3;
    --foil-soft: #f3e9e6;
    --social-square: #e9e6e4;
  }
  html, body {
    margin: 0;
    padding: 0;
    width: 1200px;
    height: 969px;
    overflow: hidden;
    background: var(--page-bg);
    font-family: "Source Sans 3", "Myriad Pro", Arial, sans-serif;
  }
  .canvas {
    position: relative;
    width: 1200px;
    height: 969px;
  }
  .business-card {
    position: absolute;
    left: 100px;
    top: 200px;
    width: 1000px;
    height: 570px;
    overflow: hidden;
    box-shadow: 0 10px 30px rgba(0,0,0,0.18);
  }
  .card-artwork {
    position: absolute;
    inset: 0;
  }
  .social-links {
    position: absolute;
    left: 60px;
    top: 36px;
    display: flex;
    gap: 10px;
  }
  .social-square {
    width: 44px;
    height: 44px;
    background: var(--social-square);
  }
  .brand-name {
    position: absolute;
    right: 74px;
    top: 62px;
    width: 420px;
    margin: 0;
    text-align: right;
    font-weight: 700;
    font-size: 60px;
    line-height: 0.98;
    letter-spacing: 1px;
    text-transform: uppercase;
    color: var(--foil);
  }
  .person {
    position: absolute;
    right: 57px;
    top: 300px;
    text-align: right;
    color: var(--foil-soft);
  }
  .person-name {
    margin: 0;
    font-weight: 600;
    font-size: 35px;
    line-height: 1.2;
  }
  .person-role {
    margin: 0;
    font-weight: 400;
    font-size: 26px;
    line-height: 1.3;
  }
  .contact-list {
    position: absolute;
    right: 57px;
    top: 400px;
    margin: 0;
    padding: 0;
    list-style: none;
    text-align: right;
    color: var(--foil-soft);
    font-size: 24px;
    line-height: 39px;
  }
  .contact-item {
    display: flex;
    align-items: center;
    justify-content: flex-end;
    gap: 14px;
  }
  .contact-icon {
    width: 24px;
    height: 24px;
    flex: none;
  }
</style>
</head>
<body>
<main class="canvas">
  <article class="business-card">
    <svg class="card-artwork" viewBox="0 0 1000 570" width="1000" height="570" aria-hidden="true">
      <defs>
        <linearGradient id="redPanel" x1="0" y1="0" x2="1" y2="1">
          <stop offset="0" stop-color="var(--card-red)"/>
          <stop offset="1" stop-color="var(--card-red-deep)"/>
        </linearGradient>
      </defs>
      <rect class="frosted-panel" x="0" y="0" width="1000" height="570" fill="var(--frost)"/>
      <polygon class="red-panel" points="302,0 1000,0 1000,570 92,570" fill="url(#redPanel)"/>
      <polygon class="accent-stripe-wide" points="282,0 296,0 86,570 72,570" fill="var(--stripe)"/>
      <polygon class="accent-stripe-thin" points="302,0 307,0 97,570 92,570" fill="var(--stripe)"/>
      <polygon class="accent-band-red" points="262,0 280,0 70,570 52,570" fill="var(--card-red)"/>
    </svg>

    <div class="social-links">
      <span class="social-square"></span>
      <span class="social-square"></span>
    </div>

    <h1 class="brand-name">Kestrel Picture House</h1>

    <div class="person">
      <p class="person-name">Teodoro Valbuena</p>
      <p class="person-role">Producer/Writer/Director</p>
    </div>

    <ul class="contact-list">
      <li class="contact-item">
        <span>555 014 2290</span>
        <svg class="contact-icon" viewBox="0 0 24 24" aria-hidden="true">
          <path d="M6.5 3h3l1.5 4.5-2 1.5a11 11 0 0 0 6 6l1.5-2 4.5 1.5v3a2 2 0 0 1-2 2A17 17 0 0 1 4.5 5a2 2 0 0 1 2-2z" fill="var(--foil-soft)"/>
        </svg>
      </li>
      <li class="contact-item">
        <span>studio@kestrelpicturehouse.example</span>
        <svg class="contact-icon" viewBox="0 0 24 24" aria-hidden="true">
          <rect x="2" y="5" width="20" height="14" fill="var(--foil-soft)"/>
          <path d="M2 5l10 8 10-8" fill="none" stroke="var(--card-red)" stroke-width="1.8"/>
        </svg>
      </li>
      <li class="contact-item">
        <span>www.kestrelpicturehouse.example</span>
        <svg class="contact-icon" viewBox="0 0 24 24" aria-hidden="true">
          <circle cx="12" cy="12" r="10" fill="var(--foil-soft)"/>
          <path d="M2 12h20M12 2c3.5 3 3.5 17 0 20M12 2c-3.5 3-3.5 17 0 20" fill="none" stroke="var(--card-red)" stroke-width="1.5"/>
        </svg>
      </li>
    </ul>
  </article>
</main>
</body>
</html>
```